Brand new redesign of Brightpath finance website

I need a new website design that i can advertise a great low interest rate on the front page and capture input application details that will send through to my email address.

some car finance companies will be similar to this would be listed below

tallowcredit.example.com.au
mirabelfinance.example.com.au
finance725.example.com.au
quenbyfinance.example.com.au
finance91.example.com.au

Reason: I have changed the project to a committed project. all the webpages should have the same format just different content and i want to be able to edit the front page easily to update my interest rates.

Target Market(s)

Australian Finance market targeting a younger demographic

Industry/Entity Type

Finance

Coding

Coded - Design and coding required

Number of Pages Required

5+ page

Font styles to use
Serif
Sans Serif

Colors
0255a3
ffffff
cedeed

Requirements
Must have
• application capture form
• apply now buttons
• Headline rate front page

```html
<!DOCTYPE html>
<html lang="en">
<head>
<meta charset="utf-8">
<title>Brightpath Finance – About Us</title>
<link href="https://fonts.googleapis.com/css2?family=Jost:wght@500;600;700&family=Lato:wght@400;700&display=swap" rel="stylesheet">
<style>
  :root{
    --brand:#0255a3;
    --brand-dark:#024a8f;
    --ink:#231f20;
    --text:#2e2e2e;
    --pale:#cedeed;
    --white:#ffffff;
    --apply-bg:#d9e6f2;
  }
  *{box-sizing:border-box;margin:0;padding:0}
  html,body{width:1200px;height:964px;overflow:hidden;background:var(--white)}
  body{font-family:'Lato',sans-serif;color:var(--text);position:relative}
  .wrap{position:absolute;left:131px;width:938px}

  .topbar{position:absolute;top:0;left:0;width:1200px;height:33px;background:var(--brand)}
  .apply-now{position:absolute;left:946px;top:0;width:123px;height:33px;background:var(--apply-bg);
    display:flex;align-items:center;gap:10px;padding-left:18px;font-size:13px;color:var(--brand);text-decoration:none}

  .header{position:absolute;top:33px;left:0;width:1200px;height:118px;background:var(--ink)}
  .brand{position:absolute;left:131px;top:30px;display:flex;align-items:center;gap:10px}
  .brand-mark{width:40px;height:40px;border-radius:50%;background:var(--brand)}
  .brand-name{font-family:'Jost',sans-serif;font-weight:600;font-size:17px;line-height:1.15;color:var(--white);letter-spacing:1px;text-transform:uppercase}
  .header-contact{position:absolute;right:131px;top:26px;display:flex;align-items:center;gap:10px}
  .header-phone{display:flex;align-items:center;gap:8px;color:#cfcfcf;font-weight:700;font-size:16px;margin-right:14px}
  .social{display:flex;gap:8px}
  .social span{width:27px;height:27px;border-radius:3px;background:var(--brand)}
  .social.light span{background:#3a78bd}
  .nav{position:absolute;right:131px;top:73px;display:flex;gap:4px}
  .nav a{font-family:'Jost',sans-serif;font-weight:600;font-size:14px;color:var(--white);text-decoration:none;
    padding:5px 13px;border-radius:2px;letter-spacing:.3px;text-transform:uppercase}
  .nav a.muted{color:#cfcfcf}
  .nav a.active{background:var(--brand)}

  .hero{position:absolute;top:151px;left:0;width:1200px;height:233px;
    background:linear-gradient(100deg,#8c1010 0%,#c8201e 25%,#e2401e 42%,#f08a2a 60%,#e8b060 78%,#b8884a 100%)}
  .hero h1{position:absolute;right:141px;top:98px;font-family:'Jost',sans-serif;font-weight:700;font-size:50px;
    color:var(--white);letter-spacing:1px;text-shadow:3px 3px 4px rgba(0,0,0,.55)}

  .content{top:432px;font-size:14.6px;line-height:24px;text-align:justify}
  .content p+p{margin-top:24px}

  .info-band{position:absolute;top:744px;left:0;width:1200px;height:137px;background:var(--pale)}
  .info{position:absolute;top:48px;display:flex;gap:12px}
  .info-icon{width:34px;height:34px;border-radius:50%;background:var(--brand);display:flex;align-items:center;justify-content:center;flex:none}
  .info h3{font-size:15.5px;font-weight:700;color:#333;text-transform:uppercase;margin-top:-2px}
  .info p{font-size:15.5px;color:#333;margin-top:5px}
  .divider{position:absolute;top:32px;width:2px;height:90px;background:linear-gradient(#cedeed,#ffffff,#cedeed)}

  .footer{position:absolute;top:881px;left:0;width:1200px;height:83px;background:var(--brand)}
  .footer-nav{position:absolute;left:132px;top:18px;display:flex;gap:17px}
  .footer-nav a{font-family:'Jost',sans-serif;font-weight:600;font-size:12.5px;color:var(--white);text-decoration:none;letter-spacing:.3px}
  .footer-nav a.muted{color:#cfdcec}
  .copyright{position:absolute;left:132px;top:45px;font-family:'Jost',sans-serif;font-weight:600;font-size:12.5px;color:var(--white);letter-spacing:.3px;text-transform:uppercase}
  .footer .social{position:absolute;right:131px;top:28px}
</style>
</head>
<body>
  <div class="topbar">
    <a class="apply-now" href="#">
      <svg width="16" height="18" viewBox="0 0 16 18"><path d="M2 1h8l4 4v12H2z" fill="none" stroke="#333" stroke-width="1.6"/><path d="M5 8h6M5 11h6M5 14h6" stroke="#333" stroke-width="1.4"/></svg>
      Apply Now
    </a>
  </div>

  <header class="header">
    <div class="brand">
      <span class="brand-mark"></span>
      <span class="brand-name">Brightpath<br>Finance</span>
    </div>
    <div class="header-contact">
      <div class="header-phone">
        <svg width="22" height="22" viewBox="0 0 24 24"><path d="M6 2l4 4-2 3c1.5 3 4 5.5 7 7l3-2 4 4-3 3C10 21 3 14 3 5z" fill="none" stroke="#cfcfcf" stroke-width="1.5"/></svg>
        1300 555 218
      </div>
      <div class="social"><span></span><span></span><span></span></div>
    </div>
    <nav class="nav">
      <a class="muted" href="#">Home</a>
      <a class="active" href="#">About</a>
      <a href="#">Vehicle Loans</a>
      <a href="#">Other Loans</a>
      <a href="#">Insurance</a>
      <a href="#">Finance Calculator</a>
      <a href="#">Contact</a>
    </nav>
  </header>

  <section class="hero" role="img" aria-label="Photo of a red car speeding along a road with golden motion-blurred light">
    <h1>ABOUT US</h1>
  </section>

  <main class="wrap content">
    <p>Lorem ipsum dolor sit amet, consectetuer adipiscing elit, sed dia nonummy laoreet dolore magna aliquam erat volutpat. Ut wisi enim ad minim veniam, quis nostrud exerci tation ullamcorper suscipit lobortis nisl ut aliquip ex eaLorem ipsum dolor sit amet, consectetuer adipiscing elit, sed dia nonummy laoreet dolore magna aliquam erat volutpat. Ut wisi enim ad minim veniam, quis nostrud exerci tation ullamcorper suscipit lobortis. Lorem ipsum dolor sit amet, consectetuer adipiscing elit, sed dia nonummy laoreet dolore magna aliquam erat volutpat. Ut wisi enim ad minim veniam, quis nostrud exerci tation ullamcorper suscipit lobortis nisl ut aliquip ex eaLorem ipsum dolor sit amet, consectetuer adipiscing elit, sed dia nonummy laoreet dolore magna aliquam erat volutpat. Ut wisi enim ad minim veniam, quis nostrud exerci tation ullamcorper suscipit lobortis</p>
    <p>Lorem ipsum dolor sit amet, consectetuer adipiscing elit, sed dia nonummy laoreet dolore magna aliquam erat volutpat. Ut wisi enim ad minim veniam, quis nostrud exerci tation ullamcorper suscipit lobortis nisl ut aliquip ex eaLorem ipsum dolor sit amet, consectetuer adipiscing elit, sed dia nonummy laoreet dolore magna aliquam erat volutpat. Ut wisi enim ad minim veniam, quis nostrud exerci tation ullamcorper suscipit lobortis. Lorem ipsum dolor sit amet, consectetuer adipiscing elit, sed dia nonummy laoreet dolore magna aliquam erat volutpat.</p>
  </main>

  <section class="info-band">
    <div class="info" style="left:131px">
      <span class="info-icon"><svg width="14" height="18" viewBox="0 0 14 18"><path d="M7 1a6 6 0 0 1 6 6c0 4-6 10-6 10S1 11 1 7a6 6 0 0 1 6-6z" fill="#fff"/><circle cx="7" cy="7" r="2.2" fill="#0255a3"/></svg></span>
      <div><h3>Brightpath Finance</h3><p>123, Lorewam Dollar, Smit Amet - 123456</p></div>
    </div>
    <span class="divider" style="left:523px"></span>
    <div class="info" style="left:580px">
      <span class="info-icon"><svg width="16" height="16" viewBox="0 0 24 24"><path d="M6 2l4 4-2 3c1.5 3 4 5.5 7 7l3-2 4 4-3 3C10 21 3 14 3 5z" fill="#fff"/></svg></span>
      <div><h3>Call Us</h3><p>1300 555 218</p></div>
    </div>
    <span class="divider" style="left:786px"></span>
    <div class="info" style="left:843px">
      <span class="info-icon"><svg width="16" height="12" viewBox="0 0 16 12"><rect x="0" y="0" width="16" height="12" rx="1" fill="#fff"/><path d="M0 1l8 6 8-6" fill="none" stroke="#0255a3" stroke-width="1.5"/></svg></span>
      <div><h3>Email Us</h3><p>info@brightpathfinance.example.com</p></div>
    </div>
  </section>

  <footer class="footer">
    <nav class="footer-nav">
      <a class="muted" href="#">HOME</a>
      <a href="#">ABOUT</a>
      <a href="#">VEHICLE LOANS</a>
      <a href="#">OTHER LOANS</a>
      <a href="#">INSURANCE</a>
      <a href="#">FINANCE CALCULATOR</a>
      <a href="#">CONTACT</a>
    </nav>
    <p class="copyright">Copyright © 2016 Brightpath Finance. All rights reserved.</p>
    <div class="social light"><span></span><span></span><span></span></div>
  </footer>
</body>
</html>
```